Brell Stone Company Business Cards

Front and Back Business Card - logo and text setup - cool design. I need workable photoshop or illustrator files so I can setup each employee card with design that is created
Updates

Hi everyone, thank you for the great entries. Please no more white and blue cards - there are so many already - black and silver only now please. thanks!

Target Market(s)

Construction Industry - Facility Managers

Industry/Entity Type

Construction

Contact Information for Business Card

I really like contemporary simplistic looks - clean neat....not opposed to seeing some black backrounds

Requirements
Must have
• Logo/website address with design on front only - www.brellstone-example.com (logo attached)
• Back:
• Name/Title/Company Address/Phone/email address
Nice to have
• Cool design
Should not have
• Nothing gimmicky like Fire or Water - since we are a Fire Protection company - it has all been done

```html
<!DOCTYPE html>
<html lang="en">
<head>
<meta charset="utf-8">
<title>Brell Stone Company – Business Cards</title>
<link href="https://fonts.googleapis.com/css2?family=Work+Sans:wght@400;500;800&display=swap" rel="stylesheet">
<style>
  :root {
    --black: #151617;
    --black-deep: #0b0b0c;
    --silver: #c3c6cb;
    --silver-dark: #8e9298;
    --silver-light: #eceef0;
    --text-light: #e6e7ea;
    --backdrop: #5b5d61;
  }
  * { margin: 0; padding: 0; box-sizing: border-box; }
  html, body { width: 1200px; height: 900px; overflow: hidden; }
  body {
    background: var(--backdrop);
    font-family: "Work Sans", Arial, sans-serif;
    position: relative;
  }
  .card {
    position: absolute;
    left: 285px;
    width: 630px;
    height: 360px;
    overflow: hidden;
    border-radius: 4px;
    background: linear-gradient(135deg, var(--black) 0%, var(--black-deep) 100%);
    box-shadow: 0 10px 28px rgba(0,0,0,.5);
  }
  .card--front { top: 50px; }
  .card--back { top: 470px; }

  /* front */
  .address {
    position: absolute; left: 150px; top: 28px;
    color: var(--text-light); font-size: 15px; line-height: 1.35; letter-spacing: .5px;
  }
  .name-band {
    position: absolute; left: 0; top: 96px; width: 420px; height: 74px;
    background: linear-gradient(90deg, var(--silver-dark), var(--silver));
    padding: 12px 0 0 70px;
    color: var(--black);
  }
  .name-band .name { font-size: 22px; font-weight: 500; letter-spacing: .5px; text-transform: uppercase; }
  .name-band .title { font-size: 15px; margin-top: 2px; }
  .contacts {
    position: absolute; left: 40px; top: 196px; list-style: none;
    color: var(--text-light); font-size: 14px; line-height: 1.6; letter-spacing: .4px;
  }
  .contacts li { display: flex; align-items: center; gap: 10px; }
  .contacts svg { width: 11px; height: 11px; fill: var(--silver); flex: none; }

  .logo-ring {
    position: absolute; left: 302px; top: 80px;
    width: 480px; height: 480px; border-radius: 50%;
    background: var(--silver-dark);
  }
  .logo-disc {
    position: absolute; left: 312px; top: 84px;
    width: 480px; height: 480px; border-radius: 50%;
    background: radial-gradient(circle at 40% 40%, #ffffff 50%, var(--silver-light) 100%);
  }
  .brand {
    position: absolute; display: flex; align-items: center; gap: 10px;
    font-weight: 800; letter-spacing: -1px;
  }
  .card--front .brand { left: 380px; top: 196px; font-size: 40px; color: var(--black); }
  .card--front .brand-mark { width: 14px; height: 14px; background: var(--silver-dark); }

  /* back */
  .card--back .brand { left: 60px; top: 135px; font-size: 76px; color: var(--silver); }
  .card--back .brand-mark { width: 26px; height: 26px; background: var(--silver-dark); }
</style>
</head>
<body>
  <section class="card card--front" aria-label="Business card front">
    <p class="address">48 Meridian Way<br>Harlow Bay, NY 10999</p>
    <div class="name-band">
      <p class="name">Daniel Harper</p>
      <p class="title">Director</p>
    </div>
    <ul class="contacts">
      <li><svg viewBox="0 0 10 10"><path d="M2 0h2l1 3-1.5 1a6 6 0 0 0 2.5 2.5L7 5l3 1v2c0 1-1 2-2 2A8 8 0 0 1 0 2c0-1 1-2 2-2z"/></svg>(555) 014-2281</li>
      <li><svg viewBox="0 0 10 10"><rect x="1" y="3" width="8" height="6" rx="1"/><rect x="3" y="0" width="4" height="4"/></svg>(555) 014-2290</li>
      <li><svg viewBox="0 0 10 10"><path d="M0 2h10v6H0z M0 2l5 3.5L10 2" stroke="#151617" stroke-width=".8"/></svg>info@brellstone-example.com</li>
      <li><svg viewBox="0 0 10 10"><circle cx="5" cy="5" r="5"/></svg>www.brellstone-example.com</li>
    </ul>
    <div class="logo-ring"></div>
    <div class="logo-disc"></div>
    <div class="brand"><span class="brand-mark"></span>Brell Stone</div>
  </section>

  <section class="card card--back" aria-label="Business card back">
    <div class="brand"><span class="brand-mark"></span>Brell Stone</div>
  </section>
</body>
</html>
```